Verdanith Website Concept

We would like a one page website. Please refer to the attached files for more information.

Please reference file attachment version 1.1.

```html
<!DOCTYPE html>
<html lang="en">
<head>
<meta charset="utf-8">
<title>Verdanith</title>
<link rel="stylesheet" href="https://fonts.googleapis.com/css2?family=Open+Sans:ital,wght@0,300;0,400;0,600;1,400&display=swap">
<style>
  :root {
    --ink: #4a4a4a;
    --ink-soft: #666;
    --brand: #3c4699;
    --brand-dark: #2f3880;
    --accent-cyan: #5cc4e6;
    --hero-dark: #161616;
    --services-bg: #efeff6;
    --contact-bg: #f2f2f2;
    --field-bg: #fafafa;
    --field-border: #cfcfcf;
    --footer-bg: #1e1e1e;
    --footer-text: #d8d8d8;
    --white: #fff;
  }
  * { box-sizing: border-box; margin: 0; padding: 0; }
  html, body { width: 1200px; height: 2198px; overflow: hidden; }
  body { font-family: "Open Sans", Arial, sans-serif; color: var(--ink); background: var(--white); }

  .site-header { height: 111px; position: relative; background: var(--white); }
  .brand { position: absolute; left: 103px; top: 28px; display: flex; align-items: center; gap: 12px; }
  .brand-mark { width: 52px; height: 52px; border-radius: 50%; background: var(--brand); }
  .brand-name { font-size: 34px; font-weight: 400; color: var(--brand); letter-spacing: 1px; }
  .main-nav { position: absolute; top: 46px; left: 651px; display: flex; gap: 40px; font-size: 14px; }
  .main-nav a { color: var(--ink-soft); text-decoration: none; }
  .main-nav a.is-active { color: var(--brand); }
  .header-divider { position: absolute; left: 915px; top: 22px; width: 1px; height: 72px; background: #ddd; }
  .call-box { position: absolute; left: 940px; top: 32px; text-align: right; width: 118px; }
  .call-label { font-size: 16px; color: var(--ink-soft); }
  .call-number { font-size: 19px; color: var(--brand); font-weight: 600; }
  .call-icon { position: absolute; left: 1066px; top: 42px; }

  .hero { position: relative; height: 446px; background: radial-gradient(ellipse at 70% 40%, #2a2a2a, var(--hero-dark) 70%); overflow: hidden; }
  .hero-photo { position: absolute; left: 610px; top: 0; width: 400px; height: 446px;
    background: linear-gradient(180deg, #3a3a3c 0%, #26272b 50%, #1a1a1c 100%); }
  .hero-copy { position: absolute; left: 103px; top: 110px; width: 480px; }
  .hero-title { font-size: 32px; font-weight: 400; color: var(--accent-cyan); margin-bottom: 12px; }
  .hero-text { font-size: 15.5px; line-height: 26.5px; color: #c8c8c8; }
  .btn-light { display: inline-block; margin-top: 14px; padding: 7px 13px; background: #e6e6e6; color: #222; font-size: 14.5px; border-radius: 3px; }
  .hero-dots { position: absolute; left: 103px; top: 428px; display: flex; gap: 9px; padding: 6px 10px; background: rgba(0,0,0,.6); border-radius: 12px; }
  .hero-dots span { width: 11px; height: 11px; border-radius: 50%; background: var(--white); }
  .hero-dots span.is-current { background: transparent; border: 2px solid var(--white); }

  .intro { height: 234px; text-align: center; padding-top: 39px; }
  .intro p { width: 860px; margin: 0 auto; font-size: 15.5px; line-height: 27px; color: var(--ink); }
  .btn-brand { display: inline-block; background: var(--brand); color: var(--white); font-size: 15px; border-radius: 3px; border: 1px solid var(--brand-dark); }
  .intro .btn-brand { margin-top: 16px; padding: 5px 13px; }

  .services { height: 440px; background: var(--services-bg); padding-top: 46px; }
  .section-title { text-align: center; font-weight: 300; color: #3b3b3b; }
  .services .section-title { font-size: 55px; line-height: 1.2; }
  .service-list { display: flex; gap: 14px; width: 1000px; margin: 36px auto 0; }
  .service { width: 239px; text-align: center; }
  .service-image { height: 158px; }
  .service-name { margin-top: 12px; font-size: 19.5px; line-height: 25px; color: var(--brand); }
  .img-risk { background: linear-gradient(160deg, #cfe6f8, #3b78c2 60%, #1e4f9a); }
  .img-chalk { background: linear-gradient(135deg, #2c2f33, #4a4f55 60%, #272a2e); }
  .img-shield { background: linear-gradient(135deg, #5a5a5a, #3a3a3a 50%, #6a6a6a); }
  .img-maint { background: linear-gradient(160deg, #1d2d44, #5c7fa8 60%, #a9bfd6); }

  .testimonials { height: 300px; padding-top: 56px; }
  .testimonials .section-title { font-size: 28px; }
  .testimonial { display: flex; width: 998px; height: 129px; margin: 22px auto 0; border: 1px solid #cfd0db; border-radius: 3px; }
  .testimonial-quote { flex: 1; display: flex; align-items: center; justify-content: center; padding: 0 28px; text-align: center; font-style: italic; font-size: 16px; line-height: 27px; color: #444; }
  .testimonial-author { position: relative; width: 182px; background: #f4f5fa; border-left: 1px solid #cfd0db; display: flex; flex-direction: column; justify-content: center; align-items: center; text-align: center; }
  .testimonial-author::before { content: ""; position: absolute; left: -11px; top: 52px; width: 20px; height: 20px; background: #f4f5fa; border-left: 1px solid #cfd0db; border-bottom: 1px solid #cfd0db; transform: rotate(45deg); }
  .author-name { font-size: 16px; font-weight: 600; color: #444; }
  .author-role { font-size: 12.5px; line-height: 17px; color: #888; margin-top: 4px; }

  .contact { height: 508px; background: var(--contact-bg); padding-top: 43px; }
  .contact-title { text-align: center; font-size: 22px; font-weight: 600; color: var(--brand); }
  .contact-form { width: 826px; margin: 22px auto 0; display: grid; grid-template-columns: repeat(3, 262px); column-gap: 20px; }
  .field { height: 34px; border: 1px solid var(--field-border); background: var(--field-bg); border-radius: 2px; padding: 0 14px; font-size: 13.5px; color: #888; display: flex; align-items: center; }
  .row-1 { margin-bottom: 18px; }
  .row-2 { margin-bottom: 19px; }
  .field-wide { grid-column: 1 / -1; margin-bottom: 23px; }
  .row-4 { margin-bottom: 23px; }
  .field-message { grid-column: 1 / -1; height: 88px; align-items: flex-start; padding-top: 12px; }
  .form-actions { grid-column: 1 / -1; text-align: center; margin-top: 31px; }
  .form-actions .btn-brand { padding: 4px 10px; font-weight: 600; font-size: 15px; }

  .site-footer { height: 159px; background: var(--footer-bg); text-align: center; padding-top: 26px; color: var(--footer-text); font-size: 15px; }
  .footer-nav a { color: var(--footer-text); text-decoration: none; }
  .footer-nav .sep { margin: 0 10px; }
  .copyright { margin-top: 12px; }
  .copyright .sep { margin: 0 14px; }
  .social { display: flex; justify-content: center; gap: 18px; margin-top: 20px; }
  .social span { width: 32px; height: 32px; border-radius: 2px; }
  .s-1 { background: #3b5a98; } .s-2 { background: #2aa3dc; } .s-3 { background: #1d78b5; }
  .s-4 { background: #f08a24; } .s-5 { background: #f06a1e; } .s-6 { background: #d8302c; }
</style>
</head>
<body>
  <header class="site-header">
    <div class="brand"><span class="brand-mark"></span><span class="brand-name">VERDANITH</span></div>
    <nav class="main-nav">
      <a href="#" class="is-active">Home</a>
      <a href="#">Services</a>
      <a href="#">Contact us</a>
    </nav>
    <div class="header-divider"></div>
    <div class="call-box">
      <div class="call-label">Call us</div>
      <div class="call-number">555 014 2290</div>
    </div>
    <svg class="call-icon" width="30" height="30" viewBox="0 0 24 24" aria-hidden="true">
      <path fill="#9a9a9a" d="M6.6 10.8a15.1 15.1 0 0 0 6.6 6.6l2.2-2.2a1 1 0 0 1 1-.25 11.4 11.4 0 0 0 3.6.57 1 1 0 0 1 1 1V20a1 1 0 0 1-1 1A17 17 0 0 1 3 4a1 1 0 0 1 1-1h3.5a1 1 0 0 1 1 1c0 1.25.2 2.45.57 3.57a1 1 0 0 1-.25 1z"/>
    </svg>
  </header>

  <section class="hero">
    <div class="hero-photo" role="img" aria-label="Smiling businessman in a dark suit holding a white piggy bank against a dark background"></div>
    <div class="hero-copy">
      <h1 class="hero-title">Welcome to Verdanith</h1>
      <p class="hero-text">Verdanith is a United States-based tier one security firm specializing in the protection of financial services professionals, executives and their families.</p>
      <span class="btn-light">Know more</span>
    </div>
    <div class="hero-dots"><span class="is-current"></span><span></span><span></span><span></span></div>
  </section>

  <section class="intro">
    <p>We manage engagements resulting from general and specific threats throughout the United States and abroad on behalf of our domestic clients. We deliver our services exclusively through associates and contractors with United States special operations, secret service, CIA, or equivalent experience and training. We are one of only a handful of domestic security firms that offers scalable, tier one security services in every market in the United States.</p>
    <span class="btn-brand">Read more</span>
  </section>

  <section class="services">
    <h2 class="section-title">OUR SERVICES</h2>
    <div class="service-list">
      <div class="service">
        <div class="service-image img-risk" role="img" aria-label="Blue road sign reading risk assessment under a bright sky"></div>
        <div class="service-name">Threat Assessment</div>
      </div>
      <div class="service">
        <div class="service-image img-chalk" role="img" aria-label="Businessman writing strengths, weaknesses, opportunities and threats on a chalkboard"></div>
        <div class="service-name">Threat Avoidance Plan<br>&amp; Dossier Creation</div>
      </div>
      <div class="service">
        <div class="service-image img-shield" role="img" aria-label="Businessman holding a protective shield icon over a family, house and car"></div>
        <div class="service-name">Elite Executive<br>Protection</div>
      </div>
      <div class="service">
        <div class="service-image img-maint" role="img" aria-label="Maintenance tab in a blue filing folder"></div>
        <div class="service-name">Threat Avoidance Plan<br>&amp; Dossier Maintenance</div>
      </div>
    </div>
  </section>

  <section class="testimonials">
    <h2 class="section-title">CLIENT’S TESTIMONIALS</h2>
    <div class="testimonial">
      <blockquote class="testimonial-quote">“ Cum sociis natoque penatibus et magnis dis parturient montes, nascetur ridiculus mus. Sed semper tristique massa at lacinia. Curabitur elementum, urna eget viverra semper, mauris diam pellentesque nisi, a egestas purus ligula at odio. Vivamus sodales dignissim dictum. ”</blockquote>
      <div class="testimonial-author">
        <div class="author-name">Marcus Hale</div>
        <div class="author-role">Pellentesque id<br>iaculis augue</div>
      </div>
    </div>
  </section>

  <section class="contact">
    <h2 class="contact-title">Contact Us</h2>
    <form class="contact-form">
      <div class="field row-1">First Name</div>
      <div class="field row-1">Last Name</div>
      <div class="field row-1">Home Phone</div>
      <div class="field row-2">Work Phone</div>
      <div class="field row-2">Cell Phone</div>
      <div class="field row-2">Email Address</div>
      <div class="field field-wide">Address</div>
      <div class="field row-4">City</div>
      <div class="field row-4">State</div>
      <div class="field row-4">Zip</div>
      <div class="field field-message">Meessage</div>
      <div class="form-actions"><span class="btn-brand">SUBMIT</span></div>
    </form>
  </section>

  <footer class="site-footer">
    <nav class="footer-nav">
      <a href="#">Home</a><span class="sep">/</span><a href="#">Services</a><span class="sep">/</span><a href="#">Contact us</a>
    </nav>
    <p class="copyright">Copyright © 2014 Verdanith. All rights reserved.<span class="sep">/</span>Privacy Policy</p>
    <div class="social">
      <span class="s-1"></span><span class="s-2"></span><span class="s-3"></span>
      <span class="s-4"></span><span class="s-5"></span><span class="s-6"></span>
    </div>
  </footer>
</body>
</html>
```